Website for IT consulting Company

I need a website upgrade, the existing site content is ok, I would also like to add a testimonial page, the site should be something that is easy for us to update content. You use the content from www.kelvanbrook.com as an example. I will also post update logo and artwork. I also need a contact form with some type of validation or captcha.

I added Coded to the Project

Please omit Address maps

Target Market(s)

small business, service oriented companies. We provide IT Consulting, support and mangement

Industry/Entity Type

Information Technology

Coding

Number of Pages Required

1 page

Font styles to use
Serif
Sans Serif

Requirements
Must have
• Contain logo attached, and content from existing web site www.kelvanbrook.com.
• Also need to update content easily, and be movable to different platforms.
• There is a catch phrase
• "Let us worry about your technology…” “ so you don’t have to!”
• Should be included.
Nice to have
• Testimonial page, Project page where we can post new and past projects and pictures
Should not have
• none

```html
<!DOCTYPE html>
<html lang="en">
<head>
<meta charset="utf-8">
<title>Kelvanbrook – IT Solutions</title>
<link rel="stylesheet" href="https://fonts.googleapis.com/css2?family=Roboto+Condensed:wght@700&family=Roboto:wght@300;400;500;700&display=swap">
<style>
:root{
  --orange:#f47b20;
  --orange-dark:#e0621a;
  --ink:#111111;
  --charcoal:#3a3a3a;
  --grey-text:#6b6b6b;
  --panel:#efeff1;
  --white:#ffffff;
  --footer:#0c0c0c;
}
*{box-sizing:border-box;margin:0;padding:0}
html,body{width:1200px;height:2965px;overflow:hidden}
body{font-family:"Roboto",Arial,sans-serif;color:var(--ink);background:var(--white);position:relative}
section,footer{position:absolute;left:0;width:1200px}

/* heading with divider */
.section-title{position:absolute;left:0;width:100%;text-align:center;font:500 31px "Roboto",sans-serif;letter-spacing:.5px}
.divider{position:absolute;height:2px;width:210px;background:var(--ink)}
.divider::after{content:"";position:absolute;left:50%;top:-5px;width:12px;height:12px;margin-left:-6px;background:var(--ink)}

/* hero */
.hero{top:0;height:682px;background:linear-gradient(180deg,#1d2a3c 0%,#243a57 40%,#1a2536 75%,#0f1520 100%);color:var(--white)}
.hero-photo{position:absolute;inset:0;background:radial-gradient(ellipse at 40% 40%,rgba(80,120,170,.35),transparent 60%)}
.brand{position:absolute;left:50px;top:16px;display:flex;align-items:center;gap:14px}
.brand-mark{width:56px;height:56px;background:var(--orange);border-radius:6px}
.brand-name{font:700 38px "Roboto",sans-serif;color:var(--white);letter-spacing:.5px;line-height:1}
.brand-tag{font:400 10px "Roboto",sans-serif;color:var(--white);margin-top:4px;opacity:.85}
.menu-toggle{position:absolute;left:1116px;top:38px;width:26px}
.menu-toggle span{display:block;height:4px;background:var(--white);margin-bottom:4px}
.hero-title{position:absolute;top:250px;width:100%;text-align:center;font:700 48px/58px "Roboto Condensed","Arial Narrow",sans-serif;text-transform:uppercase}
.hero-sub{position:absolute;top:382px;width:100%;text-align:center;font:400 17px "Roboto",sans-serif}
.play{position:absolute;left:577px;top:431px}
.btn-ghost{position:absolute;left:537px;top:498px;width:120px;height:42px;border:2px solid var(--white);border-radius:5px;color:var(--white);font:400 17px/38px "Roboto",sans-serif;text-align:center}

/* services */
.services{top:682px;height:399px}
.services .section-title{top:38px}
.services .divider{left:495px;top:92px}
.service-card{position:absolute;top:164px;height:190px;border:2px solid var(--charcoal);border-radius:10px;background:var(--white)}
.service-card.is-active{border-color:var(--orange)}
.service-icon{position:absolute;left:-28px;top:-46px;width:100px;height:100px;border-radius:10px;background:var(--charcoal);display:flex;align-items:center;justify-content:center}
.is-active .service-icon{background:var(--orange)}
.service-name{position:absolute;top:8px;font:400 17px/19px "Roboto",sans-serif;color:var(--ink)}
.service-text{position:absolute;font:400 13.5px/23px "Roboto",sans-serif;color:var(--ink)}

/* support */
.support{top:1081px;height:512px;background:var(--panel)}
.support-photo{position:absolute;left:0;top:0;width:540px;height:512px;background:linear-gradient(90deg,#4a4037 0%,#8a7460 45%,#c9bfb5 80%,var(--panel) 100%)}
.support .section-title{left:530px;width:552px;top:42px;font-size:31px}
.support .divider{left:702px;top:92px}
.support-item{position:absolute;width:320px;height:80px}
.support-icon{position:absolute;left:0;top:0;width:70px;height:70px;border:2px solid var(--charcoal);border-radius:50%;display:flex;align-items:center;justify-content:center}
.support-item.is-active .support-icon{background:var(--orange);border-color:var(--orange)}
.support-title{position:absolute;left:88px;top:2px;font:400 18px "Roboto",sans-serif;color:var(--charcoal)}
.support-item.is-active .support-title{color:var(--orange)}
.support-text{position:absolute;left:88px;top:26px;width:200px;font:400 13px/18px "Roboto",sans-serif;color:var(--charcoal)}

/* about */
.about{top:1593px;height:469px}
.about .section-title{left:0;width:1174px;top:34px}
.about .divider{left:482px;top:86px}
.about-photo{position:absolute;left:712px;top:44px;width:474px;height:356px;background:linear-gradient(135deg,#f4f4f4 0%,#d9d3cc 45%,#8f8f92 75%,#eeeeee 100%)}
.about-copy{position:absolute;left:50px;top:114px;width:680px;font:400 13.5px/26px "Roboto",sans-serif;color:var(--grey-text)}
.about-copy p{margin-bottom:8px}
.about-copy strong{color:var(--ink);font-weight:500}
.about-copy .hl{color:var(--orange)}
.btn-outline{position:absolute;left:50px;top:392px;width:104px;height:36px;border:1.5px solid var(--orange);border-radius:8px;font:400 14px/33px "Roboto",sans-serif;text-align:center;color:var(--ink)}

/* testimonials */
.testimonials{top:2062px;height:456px;background:linear-gradient(180deg,#141414,#0b0b0b 50%,#161616);color:var(--white)}
.testimonials-photo{position:absolute;inset:0;background:linear-gradient(90deg,rgba(60,60,60,.25),rgba(20,20,20,.1) 50%,rgba(70,70,70,.3))}
.testimonials .section-title{top:38px;color:var(--white)}
.testimonials .divider{left:495px;top:92px;background:var(--white)}
.testimonials .divider::after{background:var(--white)}
.quote-mark{position:absolute;width:100%;text-align:center;font:700 64px/1 Georgia,serif;color:var(--white)}
.quote-text{position:absolute;left:100px;top:200px;width:1000px;text-align:center;font:400 16px/29px "Roboto",sans-serif;color:#cfcfcf}
.quote-author{position:absolute;top:344px;width:100%;text-align:center;font:700 17px "Roboto",sans-serif}
.quote-author .sep{color:var(--orange)}
.quote-dots{position:absolute;left:563px;top:388px;display:flex;gap:8px}
.quote-dots span{width:9px;height:9px;border:1.5px solid var(--orange);transform:rotate(45deg)}

/* contact */
.contact{top:2518px;height:265px}
.contact .section-title{top:40px}
.contact .divider{left:495px;top:96px}
.field{position:absolute;height:44px;border:1.5px solid #b5b5b5;border-radius:2px;padding:12px 14px;font:400 13px "Roboto",sans-serif;color:#555}
.field-comments{height:107px}
.btn-submit{position:absolute;left:963px;top:131px;width:103px;height:105px;background:linear-gradient(180deg,#f88a3a,var(--orange-dark));border:1.5px solid #d85c14;color:var(--white);font:500 17px/105px "Roboto",sans-serif;text-align:center;letter-spacing:.5px}

/* footer */
.site-footer{top:2783px;height:182px;background:var(--footer);color:var(--white);text-align:center}
.social{position:absolute;left:488px;top:48px;display:flex;gap:7px}
.social span{width:30px;height:30px;background:#4e4e4e}
.social span:first-child{background:var(--orange)}
.footer-nav{position:absolute;top:93px;width:100%;font:400 13px "Roboto",sans-serif;color:#bbbbbb}
.footer-nav .current{color:var(--white)}
.copyright{position:absolute;top:122px;width:100%;font:400 13px "Roboto",sans-serif;color:#dddddd}
</style>
</head>
<body>

<section class="hero">
  <div class="hero-photo" role="img" aria-label="Dark blue photo of network cables plugged into a server switch"></div>
  <div class="brand">
    <div class="brand-mark"></div>
    <div>
      <div class="brand-name">KELVANBROOK</div>
      <div class="brand-tag">Let us worry about your technology… So you don't have to!</div>
    </div>
  </div>
  <div class="menu-toggle"><span></span><span></span><span></span></div>
  <h1 class="hero-title">IT Solutions that work for your<br>business a full servicetechnology company</h1>
  <p class="hero-sub">Outsourcing is subcontracting a process, such as product design or manufacturing, to a third-party company.</p>
  <svg class="play" width="46" height="46" viewBox="0 0 46 46"><circle cx="23" cy="23" r="20" fill="none" stroke="#fff" stroke-width="3"/><path d="M18 14 L32 23 L18 32 Z" fill="#fff"/></svg>
  <div class="btn-ghost">Read More</div>
</section>

<section class="services">
  <h2 class="section-title">WHAT WE &nbsp;DO</h2>
  <div class="divider"></div>

  <div class="service-card is-active" style="left:79px;width:236px">
    <div class="service-icon">
      <svg width="60" height="60" viewBox="0 0 60 60" fill="none" stroke="#fff" stroke-width="4"><circle cx="24" cy="24" r="10"/><path d="M24 6v6M24 36v6M6 24h6M36 24h6M11 11l4 4M33 33l4 4M11 37l4-4M33 15l4-4"/><circle cx="46" cy="44" r="5"/></svg>
    </div>
    <div class="service-name" style="left:105px;top:18px">Managed IT<br>Solutions</div>
    <p class="service-text" style="left:22px;top:86px;width:196px">Our staff will design, service, administer and maintain your IT needs. We are well versed on all major operating…</p>
  </div>

  <div class="service-card" style="left:376px;width:204px">
    <div class="service-icon">
      <svg width="60" height="60" viewBox="0 0 60 60" fill="none" stroke="#fff" stroke-width="4"><circle cx="30" cy="14" r="8"/><rect x="14" y="30" width="32" height="20" rx="2"/><path d="M24 54h12"/></svg>
    </div>
    <div class="service-name" style="left:112px">Remote<br>Diagnostic<br>&amp; Support</div>
    <p class="service-text" style="left:17px;top:96px;width:176px">Do you need a quick solution to a technical problem? With our live remote -assistance tool…</p>
  </div>

  <div class="service-card" style="left:643px;width:207px">
    <div class="service-icon">
      <svg width="60" height="60" viewBox="0 0 60 60" fill="none" stroke="#fff" stroke-width="4"><rect x="8" y="8" width="26" height="34" rx="2"/><path d="M14 16h14M14 24h14"/><rect x="26" y="30" width="28" height="20" rx="2"/><path d="M36 54h8"/></svg>
    </div>
    <div class="service-name" style="left:102px">Hosting<br>and<br>Virtulization</div>
    <p class="service-text" style="left:17px;top:96px;width:176px">Lorem ipsum dolor sitet, consectetur adipiscingit. Quisque pulvinar pretium interdumuisque coallis…</p>
  </div>

  <div class="service-card" style="left:911px;width:244px">
    <div class="service-icon">
      <svg width="60" height="60" viewBox="0 0 60 60" fill="none" stroke="#fff" stroke-width="4"><rect x="10" y="24" width="40" height="26" rx="2"/><path d="M20 44l18-14M26 6v12M20 12h12"/></svg>
    </div>
    <div class="service-name" style="left:103px">IT<br>Infrastructure<br>Design &amp;<br>Installation</div>
    <p class="service-text" style="left:17px;top:96px;width:212px">Do you need a quick solution to a technical problem? With our live remote-assistanc tool, a member of our support…</p>
  </div>
</section>

<section class="support">
  <div class="support-photo" role="img" aria-label="Photo of a man working on a laptop in an office"></div>
  <h2 class="section-title">IT SUPPORT SOLUTIONS</h2>
  <div class="divider"></div>

  <div class="support-item is-active" style="left:544px;top:124px">
    <div class="support-icon"><svg width="34" height="34" viewBox="0 0 34 34" fill="#fff" stroke="#fff" stroke-width="2"><circle cx="17" cy="17" r="4"/><circle cx="6" cy="8" r="3"/><circle cx="28" cy="8" r="3"/><circle cx="6" cy="26" r="3"/><circle cx="28" cy="26" r="3"/><path d="M8 10l7 5M26 10l-7 5M8 24l7-5M26 24l-7-5"/></svg></div>
    <div class="support-title">Network Adminstration</div>
    <p class="support-text">risus nec commodo porttitor, arcu ipsum imperdiet lacus,</p>
  </div>
  <div class="support-item" style="left:890px;top:124px">
    <div class="support-icon"><svg width="34" height="34" viewBox="0 0 34 34" fill="none" stroke="#3a3a3a" stroke-width="2"><rect x="4" y="6" width="20" height="16"/><path d="M10 28h8M14 22v6"/><rect x="26" y="8" width="5" height="20"/></svg></div>
    <div class="support-title">Desktop Support</div>
    <p class="support-text">Praesent consecteturant siut neque luctusnec luc</p>
  </div>
  <div class="support-item" style="left:544px;top:214px">
    <div class="support-icon"><svg width="34" height="34" viewBox="0 0 34 34" fill="none" stroke="#3a3a3a" stroke-width="2"><rect x="6" y="4" width="8" height="10"/><rect x="20" y="4" width="8" height="10"/><path d="M10 14v8c0 6 14 6 14 0v-8M17 28v4"/></svg></div>
    <div class="support-title">Netwrok Cabling</div>
    <p class="support-text">Asrit consectetur tellus nunc vitae lacusliquam phare</p>
  </div>
  <div class="support-item" style="left:890px;top:214px">
    <div class="support-icon"><svg width="34" height="34" viewBox="0 0 34 34" fill="none" stroke="#3a3a3a" stroke-width="2.5"><path d="M4 13a19 19 0 0 1 26 0M8 18a13 13 0 0 1 18 0M12 23a7 7 0 0 1 10 0"/><circle cx="17" cy="28" r="2" fill="#3a3a3a"/></svg></div>
    <div class="support-title">Wireless Network</div>
    <p class="support-text">Tus massa pulvinaraece nasnisl neque elementu</p>
  </div>
  <div class="support-item" style="left:544px;top:304px">
    <div class="support-icon"><svg width="34" height="34" viewBox="0 0 34 34" fill="#3a3a3a"><rect x="12" y="8" width="16" height="20"/><rect x="6" y="12" width="5" height="16"/><rect x="15" y="4" width="3" height="5"/></svg></div>
    <div class="support-title">Telecommunications</div>
    <p class="support-text">ta nisi enim, vitae interdum nisl euismod euusce utneque</p>
  </div>
  <div class="support-item" style="left:890px;top:304px">
    <div class="support-icon"><svg width="34" height="34" viewBox="0 0 34 34"><path d="M17 3l11 4v9c0 8-5 13-11 15C11 29 6 24 6 16V7z" fill="none" stroke="#3a3a3a" stroke-width="2.5"/><path d="M17 7v20c-4-2-7-5-7-11V9z" fill="#3a3a3a"/></svg></div>
    <div class="support-title">Antivirus Soultions</div>
    <p class="support-text">Smet massa euursus vrr ipsum Vivamus vehicula</p>
  </div>
  <div class="support-item" style="left:544px;top:392px">
    <div class="support-icon"><svg width="34" height="34" viewBox="0 0 34 34" fill="none" stroke="#3a3a3a" stroke-width="3"><circle cx="17" cy="17" r="12"/><circle cx="17" cy="17" r="5"/><path d="M9 9l4 4M25 9l-4 4M9 25l4-4M25 25l-4-4"/></svg></div>
    <div class="support-title">Disaster Recovery</div>
    <p class="support-text">Ipsum. Vestibulum a augue nisi. Nulla luctus leo mi,</p>
  </div>
  <div class="support-item" style="left:890px;top:392px">
    <div class="support-icon"><svg width="34" height="34" viewBox="0 0 34 34" fill="none" stroke="#3a3a3a" stroke-width="2"><rect x="4" y="6" width="26" height="18"/><path d="M12 30h10M17 24v6M9 12h16M9 17h10"/></svg></div>
    <div class="support-title">Web Design</div>
    <p class="support-text">Bibendum augue ac laci sagittis accums pulvinar</p>
  </div>
</section>

<section class="about">
  <div class="about-photo" role="img" aria-label="Photo of a businesswoman with a coffee cup at a laptop"></div>
  <h2 class="section-title">ABOUT US</h2>
  <div class="divider"></div>
  <div class="about-copy">
    <p><strong>Outsourcing</strong> <span class="hl">is</span> subcontracting a process, such as product design or manufacturing, to a third-party company. The decision to outsource is often made in the interest of lowering firm costs, redirecting or conserving energy directed at the competencies of a particular business, or to make more efficient use of land, labor, capital, (information) technology and resources. &nbsp;&nbsp;Outsourcing became part of the business lexicon during the 1980s.</p>
    <p>Kelvanbrook is a technology solution provider based in Houston, Texas. Our goal is to make technology a non-issue for individuals and small to medium size businesses ranging from 5 to 150 Users. Kelvanbrook has the experience, the tools, high-level technology solutions and training to power your business and your work force. We understand that all business's have one goal in common!</p>
  </div>
  <div class="btn-outline">Read More</div>
</section>

<section class="testimonials">
  <div class="testimonials-photo" role="img" aria-label="Dark background photo of business people in an office"></div>
  <h2 class="section-title">TESTIMONIALS</h2>
  <div class="divider"></div>
  <div class="quote-mark" style="top:150px">“</div>
  <p class="quote-text">We are extremely happy with our frank, open, and honest relationship with Brightline Partners. Brightline Partners' solution and delivery capabilities in the technology business not only improved the time to market and predictability, but reduced the cost of implementation</p>
  <div class="quote-mark" style="top:282px">”</div>
  <div class="quote-author">Lorem ipsum <span class="sep">|</span> Company Name</div>
  <div class="quote-dots"><span></span><span></span><span></span><span></span></div>
</section>

<section class="contact">
  <h2 class="section-title">CONTACT US</h2>
  <div class="divider"></div>
  <div class="field" style="left:128px;top:131px;width:254px">First Name:</div>
  <div class="field" style="left:401px;top:131px;width:253px">Last Name:</div>
  <div class="field field-comments" style="left:674px;top:131px;width:271px">Comments:</div>
  <div class="field" style="left:128px;top:194px;width:254px">Phone:</div>
  <div class="field" style="left:401px;top:194px;width:253px">Email:</div>
  <div class="btn-submit">SUBMIT</div>
</section>

<footer class="site-footer">
  <div class="social"><span></span><span></span><span></span><span></span><span></span><span></span></div>
  <nav class="footer-nav"><span class="current">Home</span> &nbsp;/&nbsp; About Us &nbsp;/&nbsp; Supports &nbsp;/&nbsp; Client &nbsp;/&nbsp; Careers &nbsp;/&nbsp; Contact</nav>
  <p class="copyright">© 2017. kelvanbrook.All Rights Reserved.</p>
</footer>

</body>
</html>
```